Business cards and stationary design

We just completed the design of our new logo and we need to print new business cards and letterhead for our nonprofit. We are looking for a fresh new design that shows off our new logo. On letterhead, we must have a column on the right or left to include our Board of Directors (up to 45 names) (see attachment)

Industry/Entity Type

Non-Profit

Contact Information for Business Card

Standard business card with name, title, Company name, mailing address phone numbers, email address and website. Tagline on back "Bringing the homeless home"

Font styles to use
Sans Serif

Requirements
Must have
• include pertinent information above
• new logo
• fonts compatible with logo
• should use logo colors only
Nice to have
• tag lines

```html
<!DOCTYPE html>
<html lang="en">
<head>
<meta charset="utf-8">
<title>Harbor Home Alliance – Business Card</title>
<link rel="stylesheet" href="https://fonts.googleapis.com/css2?family=Roboto:wght@300;400;500;700&display=swap">
<style>
  :root {
    --teal: #0a7f9e;
    --teal-dark: #086c87;
    --yellow: #f8b62b;
    --red: #e81c24;
    --white: #ffffff;
    --grey: #555555;
    --stage: #3b3633;
  }
  * { box-sizing: border-box; margin: 0; padding: 0; }
  html, body { width: 1200px; height: 930px; overflow: hidden; }
  body {
    background: var(--stage);
    font-family: "Roboto", Arial, sans-serif;
    position: relative;
  }
  .card {
    position: absolute;
    width: 620px;
    height: 354px;
    border-radius: 18px;
    overflow: hidden;
  }
  .card--back {
    left: 70px; top: 90px;
    background: var(--teal);
    display: flex; align-items: center; justify-content: center;
  }
  .brand {
    display: flex; align-items: center; gap: 12px;
    font-weight: 700; letter-spacing: 3px; text-transform: uppercase;
  }
  .brand__dot {
    width: 14px; height: 14px; border-radius: 50%;
  }
  .card--back .brand { color: var(--white); font-size: 26px; }
  .card--back .brand__dot { background: var(--white); width: 18px; height: 18px; }

  .card--front {
    left: 510px; top: 486px;
    background: var(--white);
  }
  .card__art { position: absolute; inset: 0; }
  .card--front .brand {
    position: absolute; right: 28px; top: 38px;
    color: var(--teal); font-size: 15px; letter-spacing: 2px;
  }
  .card--front .brand__dot { background: var(--red); }
  .person {
    position: absolute; right: 36px; top: 98px; text-align: right;
  }
  .person__name {
    color: var(--teal); font-size: 24px; font-weight: 500; letter-spacing: 0.3px;
  }
  .person__title {
    color: var(--grey); font-size: 14px; font-weight: 400; margin-top: 2px;
  }
  .contact {
    position: absolute; left: 190px; right: 24px; top: 262px;
    color: var(--white); font-size: 13px; font-weight: 300;
    text-align: center; line-height: 1.55;
  }
  .contact__label { color: var(--yellow); font-weight: 400; }
</style>
</head>
<body>

  <section class="card card--back" aria-label="Business card back">
    <div class="brand"><span class="brand__dot"></span>Harbor Home Alliance</div>
  </section>

  <section class="card card--front" aria-label="Business card front">
    <svg class="card__art" width="620" height="354" viewBox="0 0 620 354">
      <defs>
        <linearGradient id="markTone" x1="0" y1="0" x2="0" y2="1">
          <stop offset="0" stop-color="#f8b62b"/>
          <stop offset="1" stop-color="#0a7f9e"/>
        </linearGradient>
      </defs>
      <rect x="60" y="40" width="310" height="240" rx="6" fill="url(#markTone)" opacity="0.35"
            role="img" aria-label="Large brand mark artwork area"/>
      <path class="swoosh-red" d="M95,354 C150,262 330,206 620,198 L620,354 Z" fill="var(--red)"/>
      <path class="swoosh-teal" d="M138,354 C205,276 362,224 620,212 L620,354 Z" fill="var(--teal)"/>
    </svg>

    <div class="brand"><span class="brand__dot"></span>Harbor Home Alliance</div>

    <div class="person">
      <div class="person__name">DANIEL REYES</div>
      <div class="person__title">Director</div>
    </div>

    <div class="contact">
      <div><span class="contact__label">P :</span> 555.014.2290</div>
      <div><span class="contact__label">E :</span> hello@harborhome.org <span class="contact__label">| W :</span> www.harborhome.org</div>
      <div>P.O. Box 40218, Lakeview, Texas 75090</div>
    </div>
  </section>

</body>
</html>
```